Actors Postcard Design

I need a postcard designed for me. I am an actor, voice over artist and technical adviser for tv, film and videogames. I am open to color ideas. My photos are in black and white so something to make those stand out a bit. Masculine colors like dark blue etc..I have seen some of your designs with 3 photos which I liked. Perhaps a 2-3 photo scheme. Back of postcard to contain my resume. Want it to look professional and not cartoonish (since I mentioned video games). Front to have photos and job title and contact info
Updates

Please take my color direction lightly, I am open to all color schemes. light or dark. You are the professionals. Am looking forward to seeing what all of you come up with. Thanks

Industry/Entity Type

Tv

```html
<!DOCTYPE html>
<html lang="en">
<head>
<meta charset="utf-8">
<title>Tomasz Wieczorek – Resume Postcard</title>
<link rel="stylesheet" href="https://fonts.googleapis.com/css2?family=Montserrat:ital,wght@0,300;0,400;0,600;0,700;1,400&display=swap">
<style>
  :root {
    --paper: #ffffff;
    --ink-strong: #3b3b3b;
    --ink: #555555;
    --ink-soft: #7a7a7a;
    --rule: #cfcfcf;
    --photo-dark: #4a4a4a;
    --photo-mid: #7d7d7d;
    --photo-light: #a9a9a9;
  }
  * { box-sizing: border-box; margin: 0; padding: 0; }
  html, body { width: 1200px; height: 933px; overflow: hidden; background: var(--paper); }
  body { font-family: "Montserrat", sans-serif; color: var(--ink); position: relative; }

  .photo { position: absolute; left: 52px; width: 374px; }
  .photo--top { top: 54px; height: 263px; background: linear-gradient(160deg, var(--photo-dark), var(--photo-mid) 55%, var(--photo-dark)); }
  .photo--middle { top: 332px; height: 279px; background: linear-gradient(110deg, var(--photo-light), var(--photo-mid) 60%, var(--photo-dark)); }
  .photo--bottom { top: 627px; height: 249px; background: linear-gradient(180deg, var(--photo-dark), var(--photo-mid) 70%, var(--photo-dark)); }

  .name { position: absolute; left: 475px; top: 102px; color: var(--ink-strong); line-height: 1.05; }
  .name__first { font-size: 38px; font-weight: 700; letter-spacing: 1px; display: block; }
  .name__last { font-size: 38px; font-weight: 300; letter-spacing: 1px; display: block; }

  .rule { position: absolute; height: 2px; background: var(--rule); }
  .rule--stats-top { left: 475px; top: 237px; width: 620px; }
  .rule--stats-bottom { left: 475px; top: 294px; width: 620px; }

  .stats { position: absolute; left: 475px; top: 258px; width: 620px; text-align: center; font-size: 18px; font-weight: 300; color: var(--ink); word-spacing: 1px; }
  .stats b { font-weight: 600; color: var(--ink-strong); }
  .stats span { margin: 0 11px; }

  .section-title { position: absolute; left: 475px; font-size: 27px; font-weight: 700; color: var(--ink-strong); display: flex; align-items: center; }
  .section-title::after { content: ""; height: 2px; background: var(--rule); margin-left: 18px; }
  .section-title--training { top: 320px; width: 620px; }
  .section-title--training::after { flex: 1; }
  .section-title--advising { top: 565px; width: 620px; }
  .section-title--advising::after { flex: 1; }

  .section-sub { position: absolute; left: 475px; font-size: 18px; font-style: italic; color: var(--ink-strong); }
  .section-sub--training { top: 355px; }
  .section-sub--advising { top: 600px; }

  .schools { position: absolute; left: 475px; top: 402px; font-size: 15px; line-height: 21px; color: var(--ink-soft); }
  .schools b { font-weight: 600; color: var(--ink); display: block; }

  .voice { position: absolute; left: 810px; top: 390px; font-size: 15px; line-height: 21px; color: var(--ink-soft); }
  .voice__title { font-size: 17px; font-weight: 700; color: var(--ink-strong); }
  .voice__courses { margin-top: 12px; font-style: italic; font-size: 16px; line-height: 24px; }

  .block { position: absolute; left: 475px; width: 470px; font-size: 15px; line-height: 21px; color: var(--ink-soft); }
  .block--firearms { top: 650px; }
  .block--skills { top: 733px; }
  .block__title { font-size: 17px; font-weight: 700; color: var(--ink-strong); }

  .contact { position: absolute; left: 1140px; top: 873px; transform: rotate(-90deg); transform-origin: left top; white-space: nowrap; font-size: 16px; color: var(--ink-soft); }
  .contact__email { font-weight: 700; color: var(--ink-strong); margin-right: 26px; }
</style>
</head>
<body>
  <div class="photo photo--top" role="img" aria-label="Black and white headshot of the actor in a collared shirt against foliage"></div>
  <div class="photo photo--middle" role="img" aria-label="Black and white portrait of the actor in a vest outdoors"></div>
  <div class="photo photo--bottom" role="img" aria-label="Black and white portrait of the actor in a plaid shirt among trees"></div>

  <h1 class="name">
    <span class="name__first">TOMASZ</span>
    <span class="name__last">“TOM” WIECZOREK</span>
  </h1>

  <div class="rule rule--stats-top"></div>
  <p class="stats">
    <span><b>Height:</b> 6’0”</span><span><b>Weight:</b> 180</span><span><b>Hair:</b> Blond</span><span><b>Eyes:</b> Green</span>
  </p>
  <div class="rule rule--stats-bottom"></div>

  <h2 class="section-title section-title--training">Training/Experience</h2>
  <p class="section-sub section-sub--training">Acting</p>

  <div class="schools">
    <b>Harbor Lane Acting School</b>- 1.5 yrs
    <b>Stagecraft Studio Collective</b>&nbsp;– On Camera 2yrs
    <b>Highland Screen Coaching</b>– 5 day intensive
  </div>

  <div class="voice">
    <div class="voice__title">Voice Over</div>
    VoiceWorks – Daytime Conservatory<br>
    (commercial, narration, etc…)
    <div class="voice__courses">
      - Adv Daytime Conservatory<br>
      - 4 day Character Intensive
    </div>
  </div>

  <h2 class="section-title section-title--advising">Technical Advising</h2>
  <p class="section-sub section-sub--advising">Federal Special Agent – 10.5 yrs</p>

  <div class="block block--firearms">
    <span class="block__title">Extensive Firearms Training</span> – Federal, Northgate Tactics, Former Special Ops Members, Army ODA. Defensive Tactics, Breaching, Vehicle Containment, Surveillance, etc…
  </div>

  <div class="block block--skills">
    <div class="block__title">Special Skills</div>
    15 yrs martial arts (Gung Fu, Judo, Tai Chi, Kenjutsu), EMT, Personal Trainer, Scuba, Snowboarding, Snowshoeing, Alpine Mountaineering, Archery, Mountainbiking, SUP, Blacksmithing, Carpentry 7yrs. Fluent Polish.
  </div>

  <p class="contact"><span class="contact__email">tomwieczorek@mailbox.com</span>555-014-2286</p>
</body>
</html>
```